Meridale Real Estate

We are looking for help with web design for a new company that is revolutionizing the real estate world on the listing side: by charing per hour for top level professional real estate services. We would like the concept to be simple, clean and easily understood.
Updates

We want this website to actually function, not just a static design.

Industry/Entity Type

Real Estate

```html
<!DOCTYPE html>
<html lang="en">
<head>
<meta charset="utf-8">
<title>Meridale Real Estate</title>
<link href="https://fonts.googleapis.com/css2?family=PT+Sans:wght@400;700&family=Arimo:wght@400;700&display=swap" rel="stylesheet">
<style>
:root{
  --bg-header:#1c1c1c;
  --bg-band:#1f1f1f;
  --bg-side:#2a2a2a;
  --bg-mid:#242424;
  --bg-footer:#191919;
  --card-dark:#262626;
  --card-light:#dcdad5;
  --white:#ffffff;
  --muted:#8a8a8a;
  --muted-dark:#6e6e6e;
  --accent:#c5d351;
  --line:#2e2e2e;
}
*{margin:0;padding:0;box-sizing:border-box}
html,body{width:758px;height:1200px;overflow:hidden;background:var(--bg-footer)}
body{font-family:"PT Sans",sans-serif;color:var(--white);position:relative}
a{color:inherit;text-decoration:none}

/* header */
.site-header{position:absolute;left:0;top:0;width:758px;height:79px;background:var(--bg-header)}
.util-links{position:absolute;top:5px;left:597px;font-size:6px;letter-spacing:.5px;color:var(--muted)}
.util-links span{margin:0 3px}
.brand{position:absolute;left:82px;top:26px;display:flex;align-items:center;gap:6px}
.brand-mark{width:14px;height:14px;border:1.5px solid var(--white);border-radius:50%}
.brand-name{font-size:9px;letter-spacing:1.6px;text-transform:uppercase;line-height:12px;color:var(--white)}
.main-nav{position:absolute;top:49px;left:336px;display:flex;gap:20px;font-size:13px;font-weight:700;letter-spacing:.3px}

/* hero */
.hero{position:absolute;left:0;top:79px;width:758px;height:377px;
  background:linear-gradient(180deg,#7eb4e6 0%,#a9cdee 35%,#b9b09a 60%,#6f8a3c 78%,#8a6a4a 100%)}
.hero-caption{position:absolute;left:390px;top:54px;width:298px;height:136px;background:rgba(34,34,34,.88);padding:14px 6px 0 14px}
.hero-caption h1{font-family:"Arimo",sans-serif;font-size:18.5px;font-weight:700;color:var(--accent);letter-spacing:.2px;margin-bottom:8px}
.hero-caption p{font-family:"Arimo",sans-serif;font-size:9.2px;font-weight:700;line-height:14px}
.thumb-strip{position:absolute;left:157px;top:297px;width:436px;height:66px;background:#111;padding:8px 7px;display:flex;gap:1px}
.thumb{flex:1;height:50px}

/* feature cards */
.feature-band{position:absolute;left:0;top:466px;width:758px;height:259px;background:var(--bg-band)}
.side-panel{position:absolute;top:0;width:70px;height:259px;background:var(--bg-side)}
.card{position:absolute;top:0;width:138px;height:259px;padding:6px 6px 0}
.card--dark{background:var(--card-dark)}
.card--light{background:var(--card-light)}
.card-image{width:126px;height:190px}
.card-text{margin-top:18px;font-size:6px;line-height:10px;letter-spacing:.3px;color:var(--muted);text-transform:uppercase}
.card-btn{display:inline-block;margin-top:7px;font-size:6px;padding:4px 6px;letter-spacing:.4px}
.card--dark .card-btn{background:var(--card-light);color:#333}
.card--light .card-btn{background:#1b1b1b;color:var(--white)}

/* welcome / news */
.info-band{position:absolute;left:0;top:738px;width:758px;height:192px;background:var(--bg-mid)}
.info-col{position:absolute;top:26px;width:285px}
.info-col h2{font-size:14px;font-weight:400;letter-spacing:.3px;line-height:17px;margin-bottom:16px}
.tick-item{display:flex;gap:9px;margin-bottom:10px}
.tick-item svg{flex:none}
.small-copy{font-size:6px;line-height:9.5px;color:var(--muted-dark);text-transform:uppercase;letter-spacing:.2px}
.small-copy b{color:#d6d6d6;font-weight:700}
.read-more{position:absolute;top:152px;font-size:6px;letter-spacing:.5px;color:#bdbdbd}
.news-item{display:flex;gap:8px;height:32px;margin-bottom:4px}
.news-date{width:40px;flex:none;text-align:center;border-right:1px solid #3a3a3a;padding-right:4px}
.news-date strong{display:block;font-size:24px;line-height:24px;font-weight:400}
.news-date span{display:block;font-size:4.5px;line-height:7px;letter-spacing:.5px;color:var(--muted)}

/* footer */
.site-footer{position:absolute;left:0;top:930px;width:758px;height:270px;background:var(--bg-footer)}
.foot-col{position:absolute;top:34px;width:88px}
.foot-col h3{font-size:14px;font-weight:400;margin-bottom:14px}
.foot-col li{list-style:none;font-size:6px;letter-spacing:.4px;color:var(--muted-dark);text-transform:uppercase;height:19px;border-bottom:1px solid var(--line);padding-top:2px}
.foot-col li:last-child{border-bottom:none}
.foot-col li.active{color:#cfcfcf}
.newsletter-field{width:144px;height:18px;background:#111;border:1px solid #262626;position:relative}
.newsletter-field svg{position:absolute;right:-14px;top:5px}
.unsubscribe{display:inline-block;margin-top:8px;font-size:6px;color:var(--muted-dark);text-decoration:underline;letter-spacing:.4px}
.foot-brand{position:absolute;left:516px;top:140px;display:flex;align-items:center;gap:6px}
.copyright{position:absolute;left:83px;top:179px;font-family:"Arimo",sans-serif;font-size:6.5px;font-weight:700}
</style>
</head>
<body>

<header class="site-header">
  <div class="util-links"><a href="#">FAQS</a><span>|</span><a href="#">SITEMAP</a><span>|</span><a href="#">HELP</a></div>
  <a class="brand" href="#">
    <span class="brand-mark"></span>
    <span class="brand-name">Meridale<br>Real Estate</span>
  </a>
  <nav class="main-nav">
    <a href="#">HOME</a><a href="#">ABOUT US</a><a href="#">GALLERY</a><a href="#">BLOG</a><a href="#">CONTACT US</a>
  </nav>
</header>

<section class="hero" role="img" aria-label="Modern glass office building on a sunny day with autumn trees and lawn">
  <div class="hero-caption">
    <h1>MERIDALE REAL ESTATE</h1>
    <p>Lorem Ipsum has been the industry's standard dummy text ever since the 1500s, when an unknown printer took a galley of type and scrambled it to make a type specimen book. It has survived not only five centuries, but also the leap into electronic typesetting, remaining essentially unchanged</p>
  </div>
  <div class="thumb-strip">
    <div class="thumb" role="img" aria-label="House model on a green lawn against sky" style="background:linear-gradient(180deg,#3f7ed4,#9dc3ec 70%,#7bb24a)"></div>
    <div class="thumb" role="img" aria-label="City towers beside a park" style="background:linear-gradient(180deg,#5c9ee8,#c6dcf0 65%,#4c9a2e)"></div>
    <div class="thumb" role="img" aria-label="Glass skyscrapers skyline" style="background:linear-gradient(180deg,#2f6fcb,#9fc5ea 70%,#5b8f3c)"></div>
    <div class="thumb" role="img" aria-label="Villa with pool at dusk" style="background:linear-gradient(180deg,#1a3fa8,#c49a5a 60%,#3aa0c8)"></div>
    <div class="thumb" role="img" aria-label="White family house with garden" style="background:linear-gradient(180deg,#6fa8e6,#e8e4dc 60%,#4d8a2c)"></div>
  </div>
</section>

<section class="feature-band">
  <div class="side-panel" style="left:0"></div>
  <div class="side-panel" style="left:688px"></div>
  <article class="card card--dark" style="left:81px">
    <div class="card-image" role="img" aria-label="Curved white office tower against blue sky" style="background:linear-gradient(160deg,#2e6fc4,#a9c8ea 50%,#e6ecf2)"></div>
    <p class="card-text">Lorem ipsum dolor sit amet consec tetuer adipiscing elit praesent</p>
    <a class="card-btn" href="#">MORE</a>
  </article>
  <article class="card card--light" style="left:231px">
    <div class="card-image" role="img" aria-label="Glass skyscraper viewed from below" style="background:linear-gradient(160deg,#9fb3cc,#3b4e6e 50%,#1f3e8a)"></div>
    <p class="card-text">Lorem ipsum dolor sit amet consec tetuer adipiscing elit praesent</p>
    <a class="card-btn" href="#">MORE</a>
  </article>
  <article class="card card--light" style="left:381px">
    <div class="card-image" role="img" aria-label="Modern house with green roofs on a lawn" style="background:linear-gradient(180deg,#3c6a3a,#dcdcd4 50%,#5fa23a)"></div>
    <p class="card-text">Lorem ipsum dolor sit amet consec tetuer adipiscing elit praesent</p>
    <a class="card-btn" href="#">MORE</a>
  </article>
  <article class="card card--light" style="left:531px">
    <div class="card-image" role="img" aria-label="House key held up in front of a home" style="background:linear-gradient(180deg,#8ec3ea,#c8def0 60%,#9a8a7a)"></div>
    <p class="card-text">Lorem ipsum dolor sit amet consec tetuer adipiscing elit praesent</p>
    <a class="card-btn" href="#">MORE</a>
  </article>
</section>

<section class="info-band">
  <div class="info-col" style="left:82px">
    <h2>WELCOME</h2>
    <div class="tick-item">
      <svg width="17" height="17" viewBox="0 0 17 17"><circle cx="8.5" cy="8.5" r="8.5" fill="#d8d8d8"/><path d="M4.5 8.7l2.8 2.8 5.3-5.6" stroke="#242424" stroke-width="2" fill="none"/></svg>
      <p class="small-copy"><b>Lorem ipsum dolor sit amet</b> consec tetuer adipiscing elit praesent vestibulum molestie lacus. Aenean nonummy hendrerit mauris. Phasellus porta. Fusce suscipit varius mi. Cum sociis natoque penat mitra magna.</p>
    </div>
    <div class="tick-item">
      <svg width="17" height="17" viewBox="0 0 17 17"><circle cx="8.5" cy="8.5" r="8.5" fill="#d8d8d8"/><path d="M4.5 8.7l2.8 2.8 5.3-5.6" stroke="#242424" stroke-width="2" fill="none"/></svg>
      <p class="small-copy"><b>Donec accumsan malesuada orci</b> onec sit amet eros. Lorem ipsum dolor sit amet consec tetuer adipiscing elit. Mauris fermentum dictum magna. Sed laoreetor wisi et ummlisquat volutpat. Duis ac turpis. Integer rui.</p>
    </div>
  </div>
  <a class="read-more" href="#" style="left:82px">READ MORE</a>

  <div class="info-col" style="left:382px">
    <h2>NEWS</h2>
    <div class="news-item">
      <div class="news-date"><strong>23</strong><span>OCTOBER</span></div>
      <p class="small-copy">Lorem ipsum dolor sit amet consec tetuer adipiscing elit praesent vestibulum molestie lacus. Aenean nonummy hendrerit mauris. Phasellus porta. Fusce suscipit varius mi. Cum sociis natoq.</p>
    </div>
    <div class="news-item">
      <div class="news-date"><strong>07</strong><span>OCTOBER</span></div>
      <p class="small-copy">Ue penatibus et magnis dis parturientontes nascetur ridiculus mus. Nulla dui. Fusce feugiat malesuada odio. Morbi nunc odio gravida atcursus nec luctus a lorem. Maecenas tristique orci ac sem.</p>
    </div>
  </div>
  <a class="read-more" href="#" style="left:382px">READ MORE</a>
</section>

<footer class="site-footer">
  <div class="foot-col" style="left:82px">
    <h3>HOME</h3>
    <ul><li class="active">Today's news</li><li>Newsletter</li><li>Blogs</li><li>RSS feeds</li></ul>
  </div>
  <div class="foot-col" style="left:181px">
    <h3>NEWS</h3>
    <ul><li>Kitchen</li><li>Bathroom</li><li>Living room</li><li>Dining room</li><li>Bedroom</li></ul>
  </div>
  <div class="foot-col" style="left:282px">
    <h3>TIPS</h3>
    <ul><li>Product finder</li><li>Buyers' guide</li><li>Buy it now</li><li>Address books</li></ul>
  </div>
  <div class="foot-col" style="left:382px">
    <h3>ADVICE</h3>
    <ul><li>Style ideas</li><li>Buyers' guide</li><li>Most FAQs</li><li>Planning tips</li></ul>
  </div>
  <div class="foot-col" style="left:481px;width:160px">
    <h3>NEWSLETTER</h3>
    <div class="newsletter-field">
      <svg width="5" height="7" viewBox="0 0 5 7"><path d="M0 0l5 3.5L0 7z" fill="#d0d0d0"/></svg>
    </div>
    <a class="unsubscribe" href="#">UNSUBSCRIBE</a>
  </div>
  <div class="foot-brand">
    <span class="brand-mark"></span>
    <span class="brand-name">Meridale<br>Real Estate</span>
  </div>
  <p class="copyright">© Copyrights 2015 Meridale Real Estate. All Right Reserved</p>
</footer>

</body>
</html>
```